Business Card Design Project

We are looking for a new business card design to go with our new logo. We need to have a front and back card with our name and numberous phone numbers on the front and our addresses on the back. We will need to be able to edit the cards to have different names and numbers. Right now our card looks too busy and cluttered. We need to have our Brightmoor Estates Group Logo Prominently displayed. We will also need the Halvern Dunstead Portland Central, the relator logo and the equal housing logo on the front somewhere. We would like to have our addresses on the back along with the quote "Our most important goal is to exceed the expectations of our clients and the finest compliment we can received is a referral from a friend or past client. Thank you for your support!" Also, we would like the "Please follow us on : facebook logo, twitter loto, youtube logo and wordpress logo" I've attached our new logo and what our current business card looks like.

```html
<!DOCTYPE html>
<html lang="en">
<head>
<meta charset="utf-8">
<title>Brightmoor Estates Group — Business Cards</title>
<link href="https://fonts.googleapis.com/css2?family=EB+Garamond:ital,wght@0,400;0,600;0,700;1,400&display=swap" rel="stylesheet">
<style>
  :root {
    --brand-red: #b8303a;
    --brand-red-dark: #9e2630;
    --ink: #1c1c1c;
    --muted: #6b6b6b;
    --card-white: #ffffff;
    --page-bg: #ece8e2;
    --icon-grey: #d9d4cf;
  }
  * { box-sizing: border-box; margin: 0; padding: 0; }
  html, body {
    width: 1200px; height: 1000px; overflow: hidden;
    background: var(--page-bg);
    font-family: "EB Garamond", Georgia, serif;
    color: var(--ink);
  }
  .sheet {
    width: 1200px; height: 1000px;
    display: flex; justify-content: center; align-items: center; gap: 90px;
  }
  .card {
    width: 380px; height: 620px;
    background: var(--card-white);
    box-shadow: 0 6px 18px rgba(0,0,0,0.18);
    position: relative; overflow: hidden;
  }

  /* Brand name block (replaces logo) */
  .brand { text-align: center; color: var(--brand-red); font-weight: 700; }
  .brand-mark {
    width: 22px; height: 22px; border-radius: 50%;
    background: var(--brand-red); margin: 0 auto 10px;
  }
  .brand-name { font-size: 40px; line-height: 1; letter-spacing: 1px; }
  .brand-sub { font-size: 16px; letter-spacing: 3px; text-transform: uppercase; margin-top: 6px; }

  /* Back card */
  .card--back .back-top {
    height: 230px; display: flex; align-items: flex-end; justify-content: center;
    padding-bottom: 26px;
  }
  .card--back .back-body {
    position: absolute; top: 230px; left: 0; right: 0; bottom: 0;
    background: var(--brand-red); color: #fff; text-align: center;
    padding: 24px 36px 0;
  }
  .quote { font-style: italic; font-size: 15px; line-height: 1.3; }
  .address { font-weight: 600; font-size: 17px; line-height: 1.25; margin-top: 52px; }
  .follow { font-size: 17px; margin-top: 56px; }
  .social-row { display: flex; justify-content: center; gap: 16px; margin-top: 12px; }
  .social-badge {
    width: 36px; height: 36px; border-radius: 6px;
    background: var(--icon-grey); border: 2px solid #fff;
  }

  /* Front card */
  .card--front .front-logo { padding-top: 150px; }
  .card--front .brand-name { font-size: 34px; }
  .card--front .brand-sub { font-size: 13px; }
  .affiliations {
    display: flex; align-items: center; justify-content: center; gap: 14px;
    margin-top: 16px;
  }
  .broker-name { font-size: 9px; font-weight: 700; color: var(--brand-red); line-height: 1.1; width: 84px; text-align: center; }
  .badge { width: 22px; height: 22px; background: var(--ink); }
  .person { padding: 0 0 0 70px; margin-top: 34px; }
  .person-name { color: var(--brand-red); font-size: 24px; font-weight: 600; line-height: 1; }
  .person-title { color: var(--muted); font-size: 16px; margin-top: 2px; }
  .phones { list-style: none; margin-top: 22px; font-size: 17px; font-weight: 600; line-height: 1.15; }
  .phones .label { color: var(--brand-red); font-weight: 600; }
  .web { margin-top: 14px; font-size: 15px; font-weight: 700; line-height: 1.2; }
  .front-band {
    position: absolute; left: 0; right: 0; bottom: 0; height: 28px;
    background: var(--brand-red);
  }
</style>
</head>
<body>
<main class="sheet">

  <section class="card card--back" aria-label="Card back">
    <div class="back-top">
      <div class="brand">
        <div class="brand-mark"></div>
        <div class="brand-name">Brightmoor</div>
        <div class="brand-sub">Estates Group</div>
      </div>
    </div>
    <div class="back-body">
      <p class="quote">“Our most important goal is to exceed the expections of our clients and the finest compliment we can recieve is a referral from a friend or past client. Thank you for your support!”</p>
      <p class="address">118 Larchfield Court<br>2750 NE Alder Way, #310<br>Portland, OR 97230</p>
      <p class="follow">Please follow us on:</p>
      <div class="social-row">
        <span class="social-badge"></span>
        <span class="social-badge"></span>
        <span class="social-badge"></span>
        <span class="social-badge"></span>
      </div>
    </div>
  </section>

  <section class="card card--front" aria-label="Card front">
    <div class="front-logo">
      <div class="brand">
        <div class="brand-mark"></div>
        <div class="brand-name">Brightmoor</div>
        <div class="brand-sub">Estates Group</div>
      </div>
      <div class="affiliations">
        <span class="broker-name">Halvern Dunstead Portland Central</span>
        <span class="badge"></span>
        <span class="badge"></span>
      </div>
    </div>
    <div class="person">
      <p class="person-name">Clara Wendover</p>
      <p class="person-title">Broker, Listings Specialist</p>
      <ul class="phones">
        <li>(555) 214-7390 <span class="label">cell</span></li>
        <li>(555) 318-0462 <span class="label">office</span></li>
        <li>(555) 600-2187 <span class="label">toll free</span></li>
        <li>(555) 427-9813 <span class="label">fax</span></li>
      </ul>
      <p class="web">clara@brightmoorestates.com<br>www.brightmoorestates.com</p>
    </div>
    <div class="front-band"></div>
  </section>

</main>
</body>
</html>
```